VENTURE CAPITAL GROUP BUSINESS CARD DESIGN

Venture Capital Group based in SF looking for a bold business card design. No trendy colour explosion, 3D effects etc. Just "simple" optical effects. Works on your brain, keeps your eye focused and sticks to your mind.
Target Market(s)
Technology startups
Industry/Entity Type
Venture Capital
Contact Information for Business Card
DESMOND WHITLAKE
MANAGING PARTNER
187 FENWORTH ST SAN FRANCISCO, CA 94187
415.555.0142 O
415.555.0147 F
415.555.0193 C
desmond@veldtmoorcapital.ventures

```html
<!DOCTYPE html>
<html lang="en">
<head>
<meta charset="utf-8">
<title>Veldtmoor Capital Group – Business Card</title>
<link rel="stylesheet" href="https://fonts.googleapis.com/css2?family=Open+Sans:wght@400;600;700&display=swap">
<style>
  :root {
    --bg: #2b2b2b;
    --card-black: #050505;
    --card-white: #ffffff;
    --brand-green: #1e8a34;
    --accent-green: #2fb34a;
    --mark-grey: #d9d9d9;
    --text-light: #ffffff;
  }
  * { margin: 0; padding: 0; box-sizing: border-box; }
  html, body { width: 1200px; height: 900px; overflow: hidden; }
  body {
    background: var(--bg);
    font-family: "Open Sans", Arial, sans-serif;
    position: relative;
  }
  .card {
    position: absolute;
    width: 620px;
    height: 354px;
    border-radius: 22px;
    overflow: hidden;
    box-shadow: 0 14px 30px rgba(0,0,0,0.45);
  }
  .card-front { left: 150px; top: 80px; background: var(--card-black); }
  .card-back { left: 430px; top: 466px; background: var(--card-white); }

  .brand {
    position: absolute;
    display: flex;
    flex-direction: column;
    align-items: center;
    gap: 14px;
  }
  .brand-dot {
    border-radius: 50%;
    background: var(--mark-grey);
  }
  .brand-name {
    color: var(--brand-green);
    font-weight: 600;
    letter-spacing: 1px;
    text-align: center;
    line-height: 1.2;
  }
  .card-front .brand { left: 0; right: 0; top: 92px; }
  .card-front .brand-dot { width: 96px; height: 96px; }
  .card-front .brand-name { font-size: 30px; white-space: nowrap; }

  .card-back .brand { left: 400px; width: 200px; top: 66px; gap: 12px; }
  .card-back .brand-dot { width: 78px; height: 78px; }
  .card-back .brand-name { font-size: 16px; }

  .back-panel { position: absolute; inset: 0; }

  .contact {
    position: absolute;
    left: 40px;
    top: 132px;
    color: var(--text-light);
  }
  .contact-name { font-size: 22px; font-weight: 700; letter-spacing: 0.5px; }
  .contact-title {
    font-size: 12px; font-weight: 600; color: var(--accent-green);
    letter-spacing: 1px; margin-bottom: 8px;
  }
  .contact-address { font-size: 13px; line-height: 1.35; margin-bottom: 6px; }
  .contact-list { list-style: none; font-size: 13px; line-height: 1.45; }
  .contact-list li { display: flex; align-items: center; gap: 8px; }
  .contact-list svg { width: 12px; height: 12px; flex: none; }
</style>
</head>
<body>

  <section class="card card-front" aria-label="Card front">
    <div class="brand">
      <span class="brand-dot"></span>
      <span class="brand-name">VELDTMOOR CAPITAL GROUP</span>
    </div>
  </section>

  <section class="card card-back" aria-label="Card back">
    <svg class="back-panel" viewBox="0 0 620 354" preserveAspectRatio="none" aria-hidden="true">
      <path d="M0 0 H270 C345 80 375 230 330 354 H0 Z" fill="var(--card-black)"/>
      <path d="M278 0 C353 80 383 230 338 354" fill="none" stroke="var(--accent-green)" stroke-width="4"/>
    </svg>

    <div class="contact">
      <div class="contact-name">DESMOND WHITLAKE</div>
      <div class="contact-title">MANAGING PARTNER</div>
      <div class="contact-address">187 FENWORTH ST SAN<br>FRANCISCO, CA 94187</div>
      <ul class="contact-list">
        <li>
          <svg viewBox="0 0 24 24"><path fill="var(--accent-green)" d="M6.6 10.8a15 15 0 0 0 6.6 6.6l2.2-2.2a1 1 0 0 1 1-.25 11 11 0 0 0 3.6.6 1 1 0 0 1 1 1V20a1 1 0 0 1-1 1A17 17 0 0 1 3 4a1 1 0 0 1 1-1h3.5a1 1 0 0 1 1 1c0 1.25.2 2.45.6 3.6a1 1 0 0 1-.25 1z"/></svg>
          415.555.0142
        </li>
        <li>
          <svg viewBox="0 0 24 24"><rect x="4" y="8" width="16" height="10" rx="2" fill="var(--accent-green)"/><rect x="7" y="3" width="10" height="6" fill="var(--accent-green)"/></svg>
          415.555.0147
        </li>
        <li>
          <svg viewBox="0 0 24 24"><rect x="6" y="2" width="12" height="20" rx="2" fill="none" stroke="var(--accent-green)" stroke-width="2.5"/></svg>
          415.555.0193
        </li>
        <li>
          <svg viewBox="0 0 24 24"><rect x="2" y="5" width="20" height="14" rx="1" fill="none" stroke="var(--accent-green)" stroke-width="2.5"/><path d="M2 6 L12 13 L22 6" fill="none" stroke="var(--accent-green)" stroke-width="2.5"/></svg>
          desmond@veldtmoorcapital.ventures
        </li>
      </ul>
    </div>

    <div class="brand">
      <span class="brand-dot"></span>
      <span class="brand-name">VELDTMOOR<br>CAPITAL GROUP</span>
    </div>
  </section>

</body>
</html>
```